VFX Company Business Card Design Project

The Kestrel Works is a decentralized Visual Effects Studio servicing the television and feature film industries.
Project Brief:
Take our logo that was previously designed on Pencil Harbor and make a double sided business card.
Requirements:
- Card MUST be double sided.
- Front of card MUST have the yellow part of our logo against the dark grey background.
- Back of card is completely up to the designer.
- Back of card must include the complete company logo.
Please follow these File Preparation guidelines:
http://printnook.ca/infopage?file=filetype_en&s=PrintNook_new&lang=en
Business

```html
<!DOCTYPE html>
<html lang="en">
<head>
<meta charset="utf-8">
<title>The Kestrel Works – Business Card Set</title>
<link rel="stylesheet" href="https://fonts.googleapis.com/css2?family=Montserrat:wght@500;700&family=Courier+Prime&family=Bitter:wght@700&display=swap">
<style>
  :root {
    --backdrop: #cfc8be;
    --charcoal: #242424;
    --ink: #1e1e1e;
    --brand-yellow: #f8c22a;
    --slate: #5e6c6c;
    --paper: #e9efe3;
    --white: #ffffff;
    --wood-dark-top: #161616;
    --wood-dark-bottom: #303030;
  }
  * { margin: 0; padding: 0; box-sizing: border-box; }
  html, body { width: 1200px; height: 734px; overflow: hidden; }
  body { background: var(--backdrop); position: relative; font-family: "Montserrat", sans-serif; }

  .card { position: absolute; overflow: hidden; }
  .card--front { left: 67px; top: 43px; width: 523px; height: 299px; border-radius: 22px; background: var(--charcoal); }
  .card--contact { left: 628px; top: 47px; width: 525px; height: 300px; border-radius: 12px; background: var(--paper); }
  .card--light { left: 64px; top: 384px; width: 523px; height: 298px; border-radius: 22px; background: var(--paper); }
  .card--slate { left: 622px; top: 388px; width: 524px; height: 298px; border-radius: 22px; background: var(--slate); }

  .brand-name {
    position: absolute; left: 24px; right: 24px; text-align: center;
    font-family: "Montserrat", sans-serif; font-weight: 700;
    text-transform: uppercase; letter-spacing: 0; white-space: nowrap;
    line-height: 1;
  }
  .card--front .brand-name { top: 132px; font-size: 34px; color: var(--brand-yellow); }
  .card--light .brand-name { top: 132px; font-size: 32px; color: var(--ink); }
  .card--slate .brand-name { top: 116px; font-size: 35px; color: var(--white); }
  .card--contact .brand-name { top: 70px; font-size: 35px; color: var(--white); }

  .contact-header { position: absolute; left: 0; top: 0; width: 100%; height: 178px;
    background: linear-gradient(180deg, var(--wood-dark-top), var(--wood-dark-bottom)); }
  .contact-band { position: absolute; left: 0; top: 178px; width: 100%; height: 87px; background: var(--slate); color: var(--white); }
  .contact-footer { position: absolute; left: 0; top: 265px; width: 100%; height: 35px;
    font-family: "Courier Prime", monospace; font-size: 14px; color: var(--ink);
    text-align: center; line-height: 35px; letter-spacing: 0.3px; }

  .person { position: absolute; right: 308px; top: 22px; text-align: right; }
  .person__name { font-family: "Bitter", serif; font-weight: 700; font-size: 19px; line-height: 22px; }
  .person__title { font-family: "Courier Prime", monospace; font-size: 14px; line-height: 20px; }
  .divider { position: absolute; left: 230px; top: 6px; width: 1.5px; height: 60px; background: var(--white); }

  .contact-list { position: absolute; left: 244px; top: 4px; list-style: none;
    font-family: "Courier Prime", monospace; font-size: 14.5px; line-height: 19px; }
  .contact-list li { display: flex; align-items: center; gap: 5px; white-space: nowrap; }
  .contact-list svg { width: 12px; height: 12px; fill: var(--white); flex: none; }

  .web-address { position: absolute; left: 0; right: 0; text-align: center;
    font-family: "Montserrat", sans-serif; font-weight: 500; font-size: 17px; letter-spacing: 3px; }
  .card--light .web-address { top: 256px; color: var(--ink); }
  .card--slate .web-address { top: 257px; color: var(--white); }
</style>
</head>
<body>

  <section class="card card--front" aria-label="Card front">
    <div class="brand-name">The Kestrel Works</div>
  </section>

  <section class="card card--contact" aria-label="Card back with contact details">
    <div class="contact-header">
      <div class="brand-name">The Kestrel Works</div>
    </div>
    <div class="contact-band">
      <div class="person">
        <div class="person__name">Your Name</div>
        <div class="person__title">Title</div>
      </div>
      <div class="divider"></div>
      <ul class="contact-list">
        <li><svg viewBox="0 0 12 12" aria-hidden="true"><path d="M2.5 1h2l1 3-1.3 1a6 6 0 0 0 2.8 2.8L8 6.5l3 1v2A1.5 1.5 0 0 1 9.5 11 8.5 8.5 0 0 1 1 2.5 1.5 1.5 0 0 1 2.5 1z"/></svg>0987 654321</li>
        <li><svg viewBox="0 0 12 12" aria-hidden="true"><path d="M2 5l1.2-3h5.6L10 5h1v4H10v2H8.5V9h-5v2H2V9H1V5zm1.4 0h5.2l-.7-2H4.1zM2.5 6.2v1.3h1.3V6.2zm5.7 0v1.3h1.3V6.2z"/></svg>0987 654321</li>
        <li><svg viewBox="0 0 12 12" aria-hidden="true"><path d="M1 3h10v6.5H1zm1 1v.3l4 2.6 4-2.6V4zm0 1.5V8.5h8V5.5L6 8z"/></svg>info@kestrelworks.com</li>
        <li><svg viewBox="0 0 12 12" aria-hidden="true"><path d="M6 1a5 5 0 1 0 0 10A5 5 0 0 0 6 1zm0 1.2c.7.6 1.2 1.8 1.3 3.3H4.7C4.8 4 5.3 2.8 6 2.2zM2.2 6.5h1.5c.1 1.3.4 2.3 1 3a3.8 3.8 0 0 1-2.5-3zm0-1a3.8 3.8 0 0 1 2.5-3c-.6.7-.9 1.7-1 3zm2.5 1h2.6C7.2 8 6.7 9.2 6 9.8 5.3 9.2 4.8 8 4.7 6.5zm3.6 0h1.5a3.8 3.8 0 0 1-2.5 3c.6-.7.9-1.7 1-3zm0-1c-.1-1.3-.4-2.3-1-3a3.8 3.8 0 0 1 2.5 3z"/></svg>www.kestrelworks.com</li>
      </ul>
    </div>
    <div class="contact-footer">00, Complex name, City, State 0042</div>
  </section>

  <section class="card card--light" aria-label="Card back, light version">
    <div class="brand-name">The Kestrel Works</div>
    <div class="web-address">www.kestrelworks.com</div>
  </section>

  <section class="card card--slate" aria-label="Card back, slate version">
    <div class="brand-name">The Kestrel Works</div>
    <div class="web-address">www.kestrelworks.com</div>
  </section>

</body>
</html>
```